Business card for Luxury Portable Restroom Trailer company

We are a Luxury Portable Restroom Trailer Company Called FALCRIDGE HIRES. Based in Orange County California. We provide portable restroom trailers for events, such as, Weddings, Concerts, Charity events, Sporting events, Tournaments, Corporate events, ect. We rent and Sell the Luxury restrooms. Our colors are white, grey, and Orange. As you will see in the logo we uploaded.
There are 2 people in the company so the names and titles will change for the 3 people but card will remain the same. Here is the information for each Person: Dwight Penner CFO 555 318-0476
next Person: Leon Marchetti VP 555 318-0476
Next Person: Owen Marchetti CEO 555 318-0476
Information to include on the card: Luxury Restroom Trailers Rental and Sales. Weddings, Concerts, Charity, Sporting and Corp. Events.

```html
<!DOCTYPE html>
<html lang="en">
<head>
<meta charset="utf-8">
<title>Falcridge Hires – Business Card</title>
<link rel="stylesheet" href="https://fonts.googleapis.com/css2?family=Montserrat:wght@400;500;700&display=swap">
<style>
  :root {
    --stage: #1d1d20;
    --card-dark: #0b0b0b;
    --card-light: #ffffff;
    --orange: #f06a1d;
    --peach: #fbe7db;
    --ink: #2a2a2a;
    --grey: #555555;
    --white: #ffffff;
    --soft-white: #cfcfcf;
  }
  * { margin: 0; padding: 0; box-sizing: border-box; }
  html, body {
    width: 1200px; height: 900px; overflow: hidden;
    background: var(--stage);
    font-family: "Montserrat", sans-serif;
  }
  .stage {
    position: relative; width: 1200px; height: 900px;
    display: flex; flex-direction: column; align-items: center; justify-content: center; gap: 48px;
  }
  .card {
    position: relative; width: 640px; height: 366px;
    border-radius: 22px; overflow: hidden;
  }
  /* Front */
  .card-front {
    background: var(--card-dark);
    display: flex; flex-direction: column; align-items: center; justify-content: center;
  }
  .front-mark { width: 140px; height: 140px; border: 8px solid var(--white); border-radius: 50%; }
  .front-name { margin-top: 22px; color: var(--white); font-weight: 700; font-size: 30px; letter-spacing: 3px; }
  .front-tagline {
    margin-top: 12px; color: var(--orange); font-weight: 500; font-size: 15px; letter-spacing: 1px; text-align: center;
  }
  .front-events {
    margin-top: 6px; color: var(--soft-white); font-weight: 400; font-size: 13px; letter-spacing: 0.5px; text-align: center;
  }
  /* Back */
  .card-back { background: var(--card-light); }
  .back-decor {
    position: absolute; right: -70px; top: 20px; width: 360px; height: 360px;
    border: 18px solid var(--peach); border-radius: 50%;
  }
  .brand { position: absolute; left: 44px; top: 42px; display: flex; align-items: center; gap: 10px; }
  .brand-square { width: 22px; height: 22px; background: var(--orange); }
  .brand-name { color: var(--orange); font-weight: 700; font-size: 24px; letter-spacing: 1px; }
  .person { position: absolute; left: 44px; top: 118px; }
  .person-name { color: var(--orange); font-weight: 700; font-size: 26px; }
  .person-title { color: var(--grey); font-size: 14px; margin-top: 2px; letter-spacing: 1px; }
  .address { position: absolute; left: 44px; top: 188px; color: var(--ink); font-size: 14px; line-height: 1.45; font-style: normal; }
  .contacts { position: absolute; left: 44px; top: 238px; list-style: none; color: var(--ink); font-size: 14px; }
  .contacts li { display: flex; align-items: center; gap: 10px; height: 24px; }
  .contacts svg { width: 14px; height: 14px; fill: var(--orange); flex: none; }
</style>
</head>
<body>
<main class="stage">
  <section class="card card-front" aria-label="Card front">
    <div class="front-mark"></div>
    <div class="front-name">FALCRIDGE HIRES</div>
    <div class="front-tagline">Luxury Restroom Trailers Rental and Sales</div>
    <div class="front-events">Weddings, Concerts, Charity, Sporting and Corp. Events</div>
  </section>

  <section class="card card-back" aria-label="Card back">
    <div class="back-decor"></div>
    <div class="brand">
      <span class="brand-square"></span>
      <span class="brand-name">FALCRIDGE HIRES</span>
    </div>
    <div class="person">
      <div class="person-name">Owen Marchetti</div>
      <div class="person-title">CEO</div>
    </div>
    <address class="address">
      418 Harbor View Ave, #112<br>Irvine, CA 92614
    </address>
    <ul class="contacts">
      <li><svg viewBox="0 0 16 16"><path d="M3 1l3 3-1.5 2a9 9 0 005.5 5.5L12 10l3 3-2 2C7 15 1 9 1 3z"/></svg>555 318-0476</li>
      <li><svg viewBox="0 0 16 16"><path d="M4 0h8a1 1 0 011 1v14a1 1 0 01-1 1H4a1 1 0 01-1-1V1a1 1 0 011-1zm1 2v10h6V2zm3 11a1 1 0 100 2 1 1 0 000-2z"/></svg>555 318-0476</li>
      <li><svg viewBox="0 0 16 16"><path d="M1 3h14v10H1zm1 1v1l6 4 6-4V4z"/></svg>info@falcridgehires.com</li>
      <li><svg viewBox="0 0 16 16"><path d="M8 1a7 7 0 100 14A7 7 0 008 1zm0 1.5c.9.9 1.6 2.6 1.8 4.5H6.2C6.4 5.1 7.1 3.4 8 2.5zM2.6 7h2.1c.1-1.6.5-3 1.1-4A5.5 5.5 0 002.6 7zm8.7 0h2.1a5.5 5.5 0 00-3.2-4c.6 1 1 2.4 1.1 4zM2.6 9a5.5 5.5 0 003.2 4c-.6-1-1-2.4-1.1-4zm3.6 0c.2 1.9.9 3.6 1.8 4.5.9-.9 1.6-2.6 1.8-4.5zm5.1 0c-.1 1.6-.5 3-1.1 4a5.5 5.5 0 003.2-4z"/></svg>www.falcridgehires.com</li>
    </ul>
  </section>
</main>
</body>
</html>
```